Website for a financial survey consultancy

WHO WE ARE
We're a niche HR consultancy specialising in salary comparison surveys for the financial asset management industry. We position ourselves as a small, highly responsive organisation with a strong personal relationship with each of our 50+ blue-chip clients.

WHAT WE DO
Our business is 80% surveys (= products), 20% consultancy (= services). The surveys are a set of online products which clients interact with to find the information they are interested in.

WHAT WE WANT
We are completely revising our existing marketing website and need a new up-to-date look and feel for the site. We want you to design 2 web pages
- Home page
- Internal content page

More details below in Must Have Priorities.

REFERENCE SITES
- www.veltramoor.com - nice background image
- www.plimweather.com - ignoring the animations
- www.gasketvale.com
- www.quorbin.com - clean, fresh, styly but prob not corporate enough
- www.dulveropinex.com - spacious, beautiful, slightly dated tho
- www.tambly.co.uk - ignore the colours. Like the simplicity, larger font size (although want to stick with sans-serif fonts for main content)

DELIVERABLES
The final designs should be delivered as one or more PSD files with clearly named layers. All design elements and treatments should be separated out, for example use adjustment layers rather than applied (and subsequently irreversible) adjustments, strokes, shading, etc.

WHAT NEXT
I'll be monitoring the contest every day and can respond to questions fast. You can IM me on Chatterlyne or QBX.

Reason: Hi folks,

I am extending the deadline to this project as I am travelling this week and therefore will not be able to make a final decision until next Monday. I will try and provide further feedback over the course of this week but I am only going to be online occasionally so be prepared to wait a few days for a reply from me.

Thanks for all the designs so far.

Tobias

Target Market(s)

In order of importance, most important first

1. Potential customers - UK & US financial industry HR professionals, short on time. Heard about us already, want to find out more about what we do, confirm relevance for their needs. Core goal - establish credibility: are we properly resourced, will we be around for years to come, are we *real*.

2. Existing customers - UK & US financial industry professionals, short on time, under pressure, want results quickly, minimum faff, expect high quality, slickly presented information. Primary action: login and use surveys.

3. Industry professionals/researchers - probably arriving through blog content, looking to browse and hoover information. Valuable for their ability to spread awareness of who we are amongst their peers.

Industry/Entity Type

Financial

Requirements
Must have
• GENERAL
Style cues - Corporate, professional, financial, stylish, slick, clean, spacious, light
Size - standard 960px grid

NAVIGATION
- [ Home | About us | Surveys | Consulting | Blog ]
- Sub-nav (roll-over dropdown) on About Us, Surveys & Consulting

ALL PAGES
- Site navigation
- Client login (on screen permanently or link to ajaxy in-page pop-up)
- Footer section
- Existing logo (attached)* - this is obviously an important reference point in the design, esp colour

HOME PAGE
- Communicate (link thru to?) survey/consulting split
- Large photo(s)/backdrop (2-3 interchangeable options ideally). Please consider what rights agreement will be necessary for any photos you include in your design.
- Possibly bigger more prominent version of logo
- Strap line/sentence - "Focussed data is the key to success"
- 3 recent blog posts (should look good with and without blog post images)
- Free downloadable PDF research report + supporting blurb

INTERNAL PAGE
- Page title
- Content - typical page will be less than one screenfull
- Level 1 sub-heading
- Level 2 sub-heading
- Bulleted list
- Content supporting image (any image will do - interested in placement, borders (if any), spacing, caption, etc)
- 'Do something' button

* Note: there is some internal debate about this logo at the moment. Some (me) are keen for it to change, some (not me!) are not. If you have an web page design idea/concept that requires an evolution of the logo, go ahead and evolve it. We can explore this further in the design process as necessary, but don't sweat it.
Nice to have
• Values to communicate
- Knowledgeable
- Professional
- Secure
- Personal
- Experienced
- Financial industry specific
- Accurate
- Reliable
Should not have
• - Search box
- Social media links, other than RSS feed button (discrete)

```html
<!DOCTYPE html>
<html lang="en">
<head>
<meta charset="utf-8">
<title>Novarel – HR consultancy</title>
<link rel="stylesheet" href="https://fonts.googleapis.com/css2?family=Archivo+Narrow:wght@400;500&family=Arimo:wght@400;700&family=PT+Sans:wght@400;700&display=swap">
<style>
  :root {
    --stage: #333333;
    --hero-deep: #1d3a4c;
    --hero-mid: #6f9fb8;
    --hero-sky: #b7dcee;
    --hero-light: #dff1f8;
    --column: rgba(238, 247, 251, 0.86);
    --nav-top: #5f8da0;
    --nav-bottom: #41697b;
    --login-bg: #b9e2f0;
    --login-title: #3b5260;
    --login-label: #4b6270;
    --forgot: #d9eff7;
    --panel: rgba(22, 42, 46, 0.92);
    --sub-text: #b6e3f4;
    --white: #ffffff;
    --ink: #1a1f24;
    --avatar-frame: #9a9fa3;
    --avatar-fill: #8a6f5c;
    --accent: #e0561b;
    --footer: #040b10;
    --footer-link: #c9d0d4;
    --footer-muted: #8d969b;
  }
  * { box-sizing: border-box; margin: 0; padding: 0; }
  html, body { width: 1200px; height: 900px; overflow: hidden; }
  body { background: var(--stage); font-family: "Arimo", Arial, sans-serif; position: relative; }
  a { text-decoration: none; }

  .page { position: absolute; left: 121px; top: 69px; width: 964px; height: 757px; }

  .hero { position: absolute; left: 0; top: 0; width: 964px; height: 674px; overflow: hidden; }
  .hero-backdrop {
    position: absolute; inset: 0;
    background:
      radial-gradient(ellipse 160px 220px at 70px 560px, rgba(226,179,90,.75), transparent 70%),
      radial-gradient(ellipse 180px 300px at 560px 170px, rgba(255,248,225,.65), transparent 70%),
      linear-gradient(100deg, var(--hero-deep) 0%, var(--hero-mid) 35%, var(--hero-sky) 60%, var(--hero-light) 100%);
  }
  .side-column { position: absolute; left: 670px; top: 0; width: 260px; height: 674px; background: var(--column); }

  .brand { position: absolute; left: 28px; top: 40px; color: var(--white); font-size: 30px; font-weight: 400; letter-spacing: .5px; }

  .main-nav {
    position: absolute; left: 475px; top: 92px; width: 477px; height: 48px;
    background: linear-gradient(var(--nav-top), var(--nav-bottom));
    display: flex; align-items: center; justify-content: center;
    font-family: "PT Sans", Tahoma, sans-serif; font-size: 12px; color: var(--white);
  }
  .main-nav a, .main-nav .sep { color: var(--white); }
  .main-nav .sep { margin: 0 22px; }

  .login { position: absolute; left: 678px; top: 146px; width: 247px; height: 179px; background: var(--login-bg); padding: 14px 8px 0; }
  .login h2 { font-size: 14px; font-weight: 700; color: var(--login-title); margin-bottom: 9px; }
  .login label { display: block; font-size: 12px; color: var(--login-label); margin-bottom: 3px; letter-spacing: .3px; }
  .login .field { display: block; width: 225px; height: 22px; background: var(--white); border: 0; margin-bottom: 9px; }
  .login-actions { display: flex; align-items: center; gap: 5px; margin-top: 2px; }
  .login-button {
    width: 72px; height: 25px; background: var(--white); border: 2px solid #d4dbde; border-radius: 5px;
    font-family: "Arimo", Arial, sans-serif; font-size: 11px; color: var(--ink); letter-spacing: .4px;
  }
  .forgot { font-size: 11px; font-weight: 700; color: var(--forgot); }

  .blogs { position: absolute; left: 686px; top: 356px; width: 240px; }
  .blogs h2 { font-family: "Archivo Narrow", "Arial Narrow", sans-serif; font-weight: 400; font-size: 22px; color: var(--ink); margin-bottom: 13px; }
  .blog-item { display: flex; gap: 7px; height: 83px; }
  .blog-item:last-child { height: 66px; }
  .blog-avatar { flex: none; width: 52px; height: 52px; border: 3px solid var(--avatar-frame); background: linear-gradient(135deg, #c9a68c, var(--avatar-fill)); }
  .blog-text { width: 165px; font-family: "PT Sans", Tahoma, sans-serif; font-size: 11px; font-weight: 700; line-height: 14px; color: var(--ink); margin-top: -3px; letter-spacing: .2px; }
  .read-more { display: inline-block; margin-top: 7px; font-weight: 400; font-size: 11px; letter-spacing: 0; }
  .read-more a { color: var(--ink); text-decoration: underline; }
  .read-more .chev { color: var(--accent); font-weight: 700; margin-left: 3px; }
  .blog-item:last-child .read-more { margin-top: 3px; }

  .intro { position: absolute; left: 25px; top: 258px; width: 443px; height: 302px; background: var(--panel); padding: 14px 22px 0 19px; color: var(--white); }
  .intro h1 { font-family: "Archivo Narrow", "Arial Narrow", sans-serif; font-weight: 400; font-size: 70px; line-height: 70px; letter-spacing: -.3px; white-space: nowrap; }
  .intro .strap { width: 395px; font-family: "Archivo Narrow", "Arial Narrow", sans-serif; font-size: 22px; line-height: 29px; color: var(--sub-text); margin-top: 4px; }
  .intro .lead { font-size: 12.5px; line-height: 15.2px; letter-spacing: .35px; text-align: justify; hyphens: auto; -webkit-hyphens: auto; margin: 14px 0 0 5px; }

  .site-footer { position: absolute; left: 0; top: 674px; width: 964px; height: 83px; background: var(--footer); }
  .footer-nav { position: absolute; left: 24px; top: 26px; font-size: 12px; color: var(--footer-link); font-family: "PT Sans", Tahoma, sans-serif; }
  .footer-nav a, .footer-nav .sep { color: var(--footer-link); }
  .footer-nav .sep { margin: 0 23px; }
  .copyright { position: absolute; left: 24px; top: 44px; font-size: 10.5px; color: var(--footer-muted); font-family: "PT Sans", Tahoma, sans-serif; }
  .footer-brand { position: absolute; right: 28px; top: 30px; font-size: 14px; color: #e8e8e8; }
</style>
</head>
<body>
<div class="page">
  <header class="hero">
    <div class="hero-backdrop" role="img" aria-label="Photo of glass office towers rising into a bright sky"></div>
    <div class="side-column"></div>

    <a class="brand" href="#">Novarel</a>

    <nav class="main-nav">
      <a href="#">HOME</a><span class="sep">|</span>
      <a href="#">ABOUT US</a><span class="sep">|</span>
      <a href="#">SURVEYS</a><span class="sep">|</span>
      <a href="#">CONSULTING</a><span class="sep">|</span>
      <a href="#">BLOG</a>
    </nav>

    <form class="login">
      <h2>Client LOGIN</h2>
      <label for="user">User Name</label>
      <input class="field" id="user" type="text">
      <label for="pass">Password</label>
      <input class="field" id="pass" type="password">
      <div class="login-actions">
        <button class="login-button" type="button">LOGIN ››</button>
        <a class="forgot" href="#">Forgot Password?</a>
      </div>
    </form>

    <section class="blogs">
      <h2>Latest Blogs</h2>
      <article class="blog-item">
        <div class="blog-avatar" role="img" aria-label="Author portrait"></div>
        <div class="blog-text">Lorem ipsum dolor sit amet, consectetur adipiscing elit. Cras ante du<br><span class="read-more"><a href="#">Read More</a><span class="chev">»</span></span></div>
      </article>
      <article class="blog-item">
        <div class="blog-avatar" role="img" aria-label="Author portrait"></div>
        <div class="blog-text">Lorem ipsum dolor sit amet, consectetur adipiscing elit. Cras ante du<br><span class="read-more"><a href="#">Read More</a><span class="chev">»</span></span></div>
      </article>
      <article class="blog-item">
        <div class="blog-avatar" role="img" aria-label="Author portrait"></div>
        <div class="blog-text">Lorem ipsum dolor sit amet, consectetur adipiscing elit. Cras ante du<br><span class="read-more"><a href="#">Read More</a><span class="chev">»</span></span></div>
      </article>
    </section>

    <section class="intro">
      <h1>HR consultancy</h1>
      <p class="strap">specialising in salary comparison surveys for the financial asset management industry</p>
      <p class="lead">Lorem ipsum dolor sit amet, consectetur adipiscing elit. Cras ante dui, viverra non vehicula in, condimentum id ipsum. Fusce at arcu metus. Fusce eu justo nisl. Maecenas consequat condi&shy;mentum ante, quis tincidunt neque viverra sed. Aenean tempus rhoncus dolor, at dapibus ipsum dapibus at. Nulla ac turpis a quam venenatis molestie sit amet ut enim. Sed elementum feu&shy;giat bibendum. Morbi sed adipiscing tellus.</p>
    </section>
  </header>

  <footer class="site-footer">
    <nav class="footer-nav">
      <a href="#">Home</a><span class="sep">|</span>
      <a href="#">about us</a><span class="sep">|</span>
      <a href="#">Surveys</a><span class="sep">|</span>
      <a href="#">Consulting</a><span class="sep">|</span>
      <a href="#">Blog</a>
    </nav>
    <p class="copyright">© 2011 Novarel. All rights reserved</p>
    <div class="footer-brand">Novarel</div>
  </footer>
</div>
</body>
</html>
```